Mobile Fitness snd Therapy Business Card Design

I need a business card designed for my mobile fitness and therapy business.

Please view the images that I have uploaded. I like the simplicity of the design that I have attached. I adapted it with my information

Target Market(s)

Those seeking personal training, injury rehabilitation or massage therapy.

Industry/Entity Type

Business

Contact Information for Business Card

Derek Fulham - MSc, CAT(C), RMT, CSCS, Pn2
e-mail: derek@vantrelo.com
website: www.vantrelo.com
instagram: @derek_fulham

Font styles to use
Sans Serif

Colors
3176b5
0355a3

Requirements
Must have
• "Contact us to receive a FREE assessment"
• Services offered:
• Personal Training
• Golf Fitness
• Injury Rehab
• Massage Therapy
• Yoga
Nice to have
• Consistent colours with brand
• - Dark Blue: #232837
• - Blue: #5096f0
• Consistent look/feel with the website: www.vantrelo.com

```html
<!DOCTYPE html>
<html lang="en">
<head>
<meta charset="utf-8">
<title>Vantrelo Business Card</title>
<link href="https://fonts.googleapis.com/css2?family=Roboto:wght@400;500;700&family=Roboto+Condensed:wght@400;500&display=swap" rel="stylesheet">
<style>
  :root {
    --navy: #232837;
    --navy-soft: #2a3146;
    --blue: #5096f0;
    --blue-deep: #3176b5;
    --paper: #f6f6f6;
    --ink-grey: #6b6e75;
    --stage: #e7e5e1;
    --white: #ffffff;
  }
  * { box-sizing: border-box; margin: 0; padding: 0; }
  html, body { width: 1200px; height: 886px; overflow: hidden; }
  body {
    background: var(--stage);
    font-family: "Roboto", Arial, sans-serif;
    display: flex;
    flex-direction: column;
    align-items: center;
    justify-content: center;
    gap: 36px;
  }
  .card {
    position: relative;
    width: 700px;
    height: 400px;
    border-radius: 22px;
    overflow: hidden;
    box-shadow: 0 6px 18px rgba(0,0,0,0.15);
  }

  /* Back of card */
  .card-back {
    background: var(--navy);
    display: flex;
    align-items: center;
    justify-content: center;
  }
  .card-back .texture {
    position: absolute;
    inset: 0;
    background: linear-gradient(135deg, var(--navy-soft), var(--navy));
  }
  .brand-name {
    position: relative;
    font-family: "Roboto", Arial, sans-serif;
    font-weight: 700;
    letter-spacing: 4px;
    line-height: 1;
    white-space: nowrap;
  }
  .card-back .brand-name { color: var(--white); font-size: 62px; }

  /* Front of card */
  .card-front { background: var(--paper); }
  .accent-bar {
    position: absolute;
    left: 0; top: 215px;
    width: 7px; height: 120px;
    background: var(--blue);
  }
  .contact-panel {
    position: absolute;
    left: 372px; top: 46px; right: 0;
    height: 196px;
    background: var(--navy);
    border-radius: 14px 0 0 14px;
    padding: 22px 24px;
  }
  .person-name {
    font-family: "Roboto Condensed", Arial, sans-serif;
    font-weight: 500;
    font-size: 30px;
    color: var(--blue);
    line-height: 1;
  }
  .person-credentials {
    font-family: "Roboto Condensed", Arial, sans-serif;
    font-size: 13px;
    color: var(--blue);
    margin-top: 4px;
  }
  .contact-list { list-style: none; margin-top: 22px; }
  .contact-list li {
    display: flex;
    align-items: center;
    gap: 10px;
    color: var(--white);
    font-size: 17px;
    line-height: 27px;
  }
  .contact-list svg { width: 15px; height: 15px; flex: none; }

  .card-front .brand-name {
    position: absolute;
    left: 50px; top: 170px;
    color: var(--navy);
    font-size: 46px;
  }

  .offer {
    position: absolute;
    right: 36px; top: 292px;
    font-weight: 700;
    font-size: 16px;
    color: var(--blue);
    white-space: nowrap;
  }
  .services {
    position: absolute;
    right: 36px; top: 326px;
    font-size: 17px;
    color: var(--ink-grey);
    white-space: nowrap;
  }
  .services .sep { color: var(--blue); padding: 0 4px; }
</style>
</head>
<body>

  <section class="card card-back" aria-label="Card back">
    <div class="texture" role="img" aria-label="Subtle navy pattern of short rounded dashes"></div>
    <div class="brand-name">VANTRELO</div>
  </section>

  <section class="card card-front" aria-label="Card front">
    <div class="accent-bar"></div>

    <div class="contact-panel">
      <h1 class="person-name">DEREK FULHAM</h1>
      <p class="person-credentials">MSC, CAT(C), RMT, CSCS, PN2</p>
      <ul class="contact-list">
        <li>
          <svg viewBox="0 0 16 16" aria-hidden="true"><rect x="1" y="3" width="14" height="10" rx="1" fill="var(--blue)"/><path d="M1.5 3.5 8 9l6.5-5.5" fill="none" stroke="var(--navy)" stroke-width="1.4"/></svg>
          derek@vantrelo.com
        </li>
        <li>
          <svg viewBox="0 0 16 16" aria-hidden="true"><circle cx="8" cy="8" r="7" fill="var(--blue)"/><path d="M1 8h14M8 1c-3 3.5-3 10.5 0 14M8 1c3 3.5 3 10.5 0 14" fill="none" stroke="var(--navy)" stroke-width="1.1"/></svg>
          www.vantrelo.com
        </li>
        <li>
          <svg viewBox="0 0 16 16" aria-hidden="true"><circle cx="8" cy="8" r="7" fill="var(--blue)"/></svg>
          @derek_fulham
        </li>
      </ul>
    </div>

    <div class="brand-name">VANTRELO</div>

    <p class="offer">Contact us to receive a FREE assessment</p>
    <p class="services">Personal Training<span class="sep">|</span>Golf Fitness<span class="sep">|</span>Injury Rehab<span class="sep">|</span>Massage Therapy<span class="sep">|</span>Yoga</p>
  </section>

</body>
</html>
```